Mobile Fitness snd Therapy Business Card Design

I need a business card designed for my mobile fitness and therapy business.

Please view the images that I have uploaded. I like the simplicity of the design that I have attached. I adapted it with my information

Target Market(s)

Those seeking personal training, injury rehabilitation or massage therapy.

Industry/Entity Type

Business

Contact Information for Business Card

Derek Fulham - MSc, CAT(C), RMT, CSCS, Pn2
e-mail: derek@vantrelo.com
website: www.vantrelo.com
instagram: @derek_fulham

Font styles to use
Sans Serif

Colors
3176b5
0355a3

Requirements
Must have
• "Contact us to receive a FREE assessment"
• Services offered:
• Personal Training
• Golf Fitness
• Injury Rehab
• Massage Therapy
• Yoga
Nice to have
• Consistent colours with brand
• - Dark Blue: #232837
• - Blue: #5096f0
• Consistent look/feel with the website: www.vantrelo.com

```html
<!DOCTYPE html>
<html lang="en">
<head>
<meta charset="utf-8">
<title>Vantrelo Business Card</title>
<link href="https://fonts.googleapis.com/css2?family=Roboto:wght@400;500;700;900&family=Roboto+Condensed:wght@700&display=swap" rel="stylesheet">
<style>
  :root {
    --navy: #232837;
    --brand-blue: #3176b5;
    --bright-blue: #2f5fd6;
    --card-white: #f7f7f7;
    --ink: #1f2533;
    --muted: #4a4f5c;
    --stage: #e4e2de;
  }
  * { box-sizing: border-box; margin: 0; padding: 0; }
  html, body {
    width: 1200px; height: 886px; overflow: hidden;
    background: var(--stage);
    font-family: "Roboto", Arial, sans-serif;
  }
  .stage {
    width: 1200px; height: 886px;
    display: flex; flex-direction: column; align-items: center; justify-content: center;
    gap: 40px;
  }
  .card {
    position: relative;
    width: 620px; height: 354px;
    border-radius: 22px;
    box-shadow: 0 10px 28px rgba(0,0,0,.18);
    overflow: hidden;
  }
  .card--front { background: var(--navy); color: #fff; }
  .card--back { background: var(--card-white); color: var(--ink); }

  .wordmark { position: absolute; }
  .wordmark__name {
    display: flex; align-items: center; gap: 12px;
    font-weight: 900; font-size: 50px; letter-spacing: 6px; line-height: 1;
    text-transform: uppercase;
  }
  .wordmark__square {
    width: 14px; height: 14px; background: var(--bright-blue); flex: none;
  }
  .wordmark__tagline {
    margin-top: 8px; margin-left: 26px;
    font-weight: 700; font-size: 13px; letter-spacing: 3.4px; text-transform: uppercase;
  }
  .card--front .wordmark { left: 148px; top: 98px; }
  .card--front .wordmark__name { color: #fff; }
  .card--front .wordmark__tagline { color: #fff; }
  .card--back .wordmark { left: 56px; top: 70px; }
  .card--back .wordmark__name { color: var(--ink); }
  .card--back .wordmark__tagline { color: var(--ink); }

  .offer {
    position: absolute; left: 50%; top: 206px; transform: translateX(-50%);
    background: var(--bright-blue); color: #fff;
    border-radius: 20px; padding: 8px 22px;
    font-weight: 700; font-size: 17px; letter-spacing: .3px; white-space: nowrap;
    text-transform: uppercase;
  }
  .services {
    position: absolute; left: 0; right: 0; top: 254px;
    text-align: center; font-size: 13.5px; color: #fff; white-space: nowrap;
  }
  .services__sep { color: var(--bright-blue); margin: 0 6px; }

  .person { position: absolute; left: 56px; bottom: 58px; color: var(--bright-blue); }
  .person__name {
    font-family: "Roboto Condensed", "Roboto", sans-serif;
    font-weight: 700; font-size: 30px; text-transform: uppercase; line-height: 1;
  }
  .person__credentials {
    margin-top: 6px;
    font-family: "Roboto Condensed", "Roboto", sans-serif;
    font-weight: 700; font-size: 13px; letter-spacing: .3px;
  }

  .contacts { position: absolute; right: 48px; top: 150px; list-style: none; }
  .contacts__item {
    display: flex; align-items: center; gap: 9px;
    font-size: 14px; color: var(--muted); margin-bottom: 9px;
  }
  .contacts__icon { width: 15px; height: 15px; flex: none; }
</style>
</head>
<body>
<main class="stage">
  <section class="card card--front" aria-label="Card front">
    <div class="wordmark">
      <div class="wordmark__name"><span class="wordmark__square"></span>Vantrelo</div>
      <div class="wordmark__tagline">Nutrition - Fitness - Health</div>
    </div>
    <p class="offer">Contact us to receive a free assessment</p>
    <p class="services">
      Personal Training<span class="services__sep">|</span>Golf Fitness<span class="services__sep">|</span>Injury Rehab<span class="services__sep">|</span>Massage Therapy<span class="services__sep">|</span>Yoga
    </p>
  </section>

  <section class="card card--back" aria-label="Card back">
    <div class="wordmark">
      <div class="wordmark__name"><span class="wordmark__square"></span>Vantrelo</div>
      <div class="wordmark__tagline">Nutrition - Fitness - Health</div>
    </div>

    <ul class="contacts">
      <li class="contacts__item">
        <svg class="contacts__icon" viewBox="0 0 16 16" aria-hidden="true">
          <rect x="1" y="3" width="14" height="10" rx="1.5" fill="#2f5fd6"/>
          <path d="M1.5 4 L8 9 L14.5 4" fill="none" stroke="#fff" stroke-width="1.4"/>
        </svg>
        derek@vantrelo.com
      </li>
      <li class="contacts__item">
        <svg class="contacts__icon" viewBox="0 0 16 16" aria-hidden="true">
          <circle cx="8" cy="8" r="7" fill="#2f5fd6"/>
          <ellipse cx="8" cy="8" rx="3" ry="6.5" fill="none" stroke="#fff" stroke-width="1.1"/>
          <line x1="1.5" y1="8" x2="14.5" y2="8" stroke="#fff" stroke-width="1.1"/>
        </svg>
        www.vantrelo.com
      </li>
      <li class="contacts__item">
        <svg class="contacts__icon" viewBox="0 0 16 16" aria-hidden="true">
          <circle cx="8" cy="8" r="7" fill="#2f5fd6"/>
        </svg>
        @derek_fulham
      </li>
    </ul>

    <div class="person">
      <h1 class="person__name">Derek Fulham</h1>
      <p class="person__credentials">MSc, CAT(C), RMT, CSCS, Pn2</p>
    </div>
  </section>
</main>
</body>
</html>
```